Campaign: « Hellere Wege entdecken », « Discover brighter paths »

We would like to start a campaign for which we need a good visual appearance. So it's about creating a key visual that represents the activities around the campaign. The campaign « Hellere Wege entdecken » in english « Discover brighter paths » aims to make a valuable contribution to social integration and to counteract social isolation. More in the briefing.

Target Market(s)

Switzerland, Berne

Industry/Entity Type

Non Profit, NGO

Font styles to use
Sans Serif
Other font styles liked:
• Helvetica neue

Colors

Designer to choose colors to be used in the design.

```html
<!DOCTYPE html>
<html lang="de">
<head>
<meta charset="utf-8">
<title>Cheer Together – Hellere Wege entdecken</title>
<link rel="stylesheet" href="https://fonts.googleapis.com/css2?family=Archivo:wght@900&family=Poppins:wght@500&display=swap">
<style>
  :root {
    --crimson-deep: #6e0714;
    --crimson: #9a0f1f;
    --red-bright: #d8222b;
    --red-glow: #e8383a;
    --ink: #160709;
    --ink-soft: #3a0d12;
    --white: #ffffff;
  }
  * { margin: 0; padding: 0; box-sizing: border-box; }
  html, body {
    width: 1200px;
    height: 1200px;
    overflow: hidden;
    background: var(--crimson-deep);
  }
  .key-visual {
    position: relative;
    width: 1200px;
    height: 1200px;
    overflow: hidden;
  }
  .crowd-photo {
    position: absolute;
    inset: 0;
    background:
      radial-gradient(ellipse 60% 45% at 50% 48%, var(--red-glow) 0%, transparent 70%),
      radial-gradient(ellipse 35% 25% at 78% 30%, rgba(232, 56, 58, 0.7) 0%, transparent 70%),
      radial-gradient(ellipse 35% 25% at 20% 35%, rgba(216, 34, 43, 0.7) 0%, transparent 70%),
      linear-gradient(180deg, var(--crimson) 0%, var(--red-bright) 45%, var(--crimson) 75%, var(--crimson-deep) 100%);
  }
  .headline {
    position: absolute;
    left: 0;
    top: 0;
    width: 1200px;
    height: 1200px;
  }
  .headline text {
    font-family: "Archivo", "Helvetica Neue", Arial, sans-serif;
    font-weight: 900;
    font-size: 232px;
    letter-spacing: -6px;
    fill: url(#headline-fill);
    stroke: var(--white);
    stroke-width: 3;
    paint-order: stroke;
  }
  .brand {
    position: absolute;
    left: 0;
    right: 0;
    top: 1074px;
    display: flex;
    justify-content: center;
    align-items: center;
    gap: 18px;
  }
  .brand-dot {
    width: 72px;
    height: 72px;
    border-radius: 50%;
    background: var(--white);
    flex: none;
  }
  .brand-name {
    font-family: "Poppins", "Helvetica Neue", Arial, sans-serif;
    font-weight: 500;
    font-size: 27px;
    letter-spacing: 1px;
    text-transform: uppercase;
    color: var(--white);
  }
</style>
</head>
<body>
<main class="key-visual">
  <div class="crowd-photo" role="img" aria-label="Photo of a group of fans in red jackets cheering loudly together on a coach bus, bathed in a red colour tint"></div>

  <svg class="headline" viewBox="0 0 1200 1200" aria-label="Cheer Together">
    <defs>
      <linearGradient id="headline-fill" x1="0" y1="0" x2="0" y2="1">
        <stop offset="0" stop-color="var(--ink)"/>
        <stop offset="1" stop-color="var(--ink-soft)"/>
      </linearGradient>
    </defs>
    <text x="588" y="601" text-anchor="middle">Cheer</text>
    <text x="614" y="780" text-anchor="middle">Together</text>
  </svg>

  <div class="brand">
    <span class="brand-dot" aria-hidden="true"></span>
    <span class="brand-name">Hellere Wege entdecken</span>
  </div>
</main>
</body>
</html>
```